Veterinary Pylon

My veterinary clinic is not clearly visible from the street and I want to place a Pylon next to my driveway. I want a modern, elegant straight Design, the Photo shows the sheduled place. One can see the clinic on our Homepage: www.tailbright-vethaus.at
The last pictures are examples for pylones I like

Target Market(s)

the passing cars often miss my entry...I want to show where to turn left

Colors
3276b5
33a6d7
00a990

Requirements
Must have
• High value, simple elegance, size: 250cm (high) x 100cm (width)
Nice to have
• Our Logo, arrow(?)

A special Text is not necessary but this will be an option:

Biegen sie hier ab und wir biegen es wieder hin!
Should not have
• Too much Color, the colors I have chosen are the possible colors but it‘s not necessary to use them.

```html
<!DOCTYPE html>
<html lang="de">
<head>
<meta charset="utf-8">
<title>Tailbright Vethaus – Pylon</title>
<link href="https://fonts.googleapis.com/css2?family=Montserrat:wght@500;600;700&display=swap" rel="stylesheet">
<style>
  :root {
    --navy: #29498a;
    --sky: #41b8dc;
    --white: #ffffff;
    --backdrop: #eef1f4;
  }
  * { box-sizing: border-box; margin: 0; padding: 0; }
  html, body { width: 818px; height: 1200px; overflow: hidden; }
  body {
    position: relative;
    background: var(--backdrop);
    font-family: "Montserrat", Arial, sans-serif;
  }
  .pylon-shape { position: absolute; left: 0; top: 0; }
  .brand-panel {
    position: absolute;
    left: 106px; top: 335px;
    width: 606px; height: 220px;
    background: var(--white);
    padding: 12px;
  }
  .brand-frame {
    width: 100%; height: 100%;
    border: 2px solid var(--navy);
    display: flex; align-items: center; justify-content: center; gap: 18px;
  }
  .brand-dot {
    width: 34px; height: 34px; border-radius: 50%;
    background: var(--sky);
  }
  .brand-name {
    color: var(--navy);
    font-weight: 700;
    font-size: 42px;
    letter-spacing: 0.5px;
  }
  .headline {
    position: absolute;
    left: 251px; top: 586px;
    color: var(--white);
    font-weight: 700;
    font-size: 37px;
    line-height: 44px;
  }
  .hours {
    position: absolute;
    left: 252px; top: 752px;
    list-style: none;
  }
  .hours-block {
    border-left: 2px solid var(--white);
    padding-left: 9px;
    height: 62px;
    margin-bottom: 18px;
  }
  .hours-day {
    color: var(--sky);
    font-weight: 600;
    font-size: 16px;
    line-height: 20px;
    letter-spacing: 0.3px;
  }
  .hours-time {
    color: var(--white);
    font-weight: 500;
    font-size: 16.5px;
    line-height: 20.5px;
  }
  .web-address {
    position: absolute;
    left: 252px; top: 1002px;
    color: var(--white);
    font-weight: 600;
    font-size: 21px;
  }
</style>
</head>
<body>
  <svg class="pylon-shape" width="818" height="1200" viewBox="0 0 818 1200" aria-hidden="true">
    <polygon points="203,162 328,223 203,285" fill="var(--sky)"/>
    <polygon points="203,285 615,85 615,1115 203,1115" fill="var(--navy)"/>
    <polygon points="615,1025 615,1115 432,1115" fill="var(--sky)"/>
  </svg>

  <div class="brand-panel">
    <div class="brand-frame">
      <span class="brand-dot"></span>
      <span class="brand-name">Tailbright Vethaus</span>
    </div>
  </div>

  <h1 class="headline">Biegen Sie ein,<br>dann biegen wir<br>es hin!</h1>

  <ul class="hours">
    <li class="hours-block">
      <p class="hours-day">MONDAY - FRIDAY</p>
      <p class="hours-time">08:00 - 12:00</p>
      <p class="hours-time">14:00 - 19:00</p>
    </li>
    <li class="hours-block">
      <p class="hours-day">SATURDAY</p>
      <p class="hours-time">08:00 - 12:00</p>
      <p class="hours-time">17:00 - 18:00</p>
    </li>
    <li class="hours-block">
      <p class="hours-day">SUNDAY</p>
      <p class="hours-time">10:00 am - 11:00 am</p>
      <p class="hours-time">17:00 - 18:00</p>
    </li>
  </ul>

  <p class="web-address">www.tailbright-vethaus.at</p>
</body>
</html>
```